Quick Straightforward Billboard Redesign

- Design billboard sized for 10 foot' x 36' foot width live area size and please include bleeds 6" around all sides
- Exact blue color match is imperative in headline, logo, phone number bubble or wherever used. C-83 / M-45 / Y-1 / K-0-
- What I hope to illustrate is that our company offers the best porch screening in the area area, in regards to quality, expertise, durability, storms proof, but we do not build screen porches.
- Current board is attached below from previous designer, and as you can see sizing was off, white space on edges make it appear to be sized incorrectly.
- I also attached my own little mock up idea well well if it helps, favorite image, logo, headline, etc and ideas perhaps on expanding or making this better?

Thanks so much!

Target Market(s)

Drivers and passengers, Southeastern NC, are of immense new construction and high end homes.

Industry/Entity Type

Construction

Colors
0054AA
0677BA
7BADD7
CADEEF
E8F1F8

Requirements
Must have
• Blue color matching
Nice to have
• Design spins or other thoughts on my little mock up

```html
<!DOCTYPE html>
<html lang="en">
<head>
<meta charset="utf-8">
<title>Harborview Screening Billboard</title>
<link href="https://fonts.googleapis.com/css2?family=Anton&display=swap" rel="stylesheet">
<style>
  :root {
    --backdrop: #7e848a;
    --paper: #ffffff;
    --brand-blue: #0a67b4;
    --brand-green: #06b65a;
    --phone-text: #f4efe2;
    --icon-green: #10b25a;
    --sky: #9cc7ea;
    --trees: #5f8f4e;
    --patio: #b9b4ab;
    --porch-ceiling: #eef0ef;
  }
  html, body {
    margin: 0;
    padding: 0;
    width: 1200px;
    height: 461px;
    overflow: hidden;
    background: var(--backdrop);
  }
  .billboard {
    position: absolute;
    left: 66px;
    top: 65px;
    width: 1074px;
    height: 323px;
    box-shadow: 0 6px 14px rgba(0,0,0,0.35);
  }
  .billboard svg { display: block; }
  .headline { font-family: "Anton", "Impact", sans-serif; }
  .headline-primary { fill: var(--brand-blue); }
  .headline-secondary { fill: var(--brand-green); }
  .phone-number { font-family: "Anton", "Impact", sans-serif; fill: var(--phone-text); }
  .company-name { font-family: "Anton", "Impact", sans-serif; fill: var(--brand-blue); }
</style>
</head>
<body>
  <div class="billboard">
    <svg width="1074" height="323" viewBox="0 0 1074 323" xmlns="http://www.w3.org/2000/svg">
      <defs>
        <linearGradient id="porch-photo-tones" x1="0" y1="0" x2="0" y2="1">
          <stop offset="0" stop-color="var(--porch-ceiling)"/>
          <stop offset="0.22" stop-color="#dfe6ea"/>
          <stop offset="0.38" stop-color="var(--sky)"/>
          <stop offset="0.5" stop-color="var(--trees)"/>
          <stop offset="0.66" stop-color="#7d715f"/>
          <stop offset="1" stop-color="var(--patio)"/>
        </linearGradient>
        <clipPath id="photo-area">
          <polygon points="816,0 1074,0 1074,323 681,323"/>
        </clipPath>
      </defs>

      <rect class="canvas-fill" width="1074" height="323" fill="var(--paper)"/>

      <!-- headline -->
      <text class="headline headline-primary" x="33" y="103" font-size="88" textLength="654" lengthAdjust="spacingAndGlyphs">Screen your Porch.</text>
      <text class="headline headline-secondary" x="33" y="186" font-size="88" textLength="600" lengthAdjust="spacingAndGlyphs">Built for the Coast.</text>

      <!-- phone bubble -->
      <path class="phone-bubble" d="M0,215 H374 a17,17 0 0 1 17,17 V278 a17,17 0 0 1 -17,17 H0 Z" fill="var(--brand-blue)"/>
      <circle cx="52" cy="255" r="22" fill="var(--paper)"/>
      <circle cx="52" cy="255" r="18" fill="var(--icon-green)"/>
      <path class="phone-icon" d="M44,246 c1.5,-1.5 3,-1 4,0.5 l2,3 c0.8,1.3 0.3,2.5 -0.8,3.3 l-1,0.8 c1,2.5 3,4.5 5.5,5.5 l0.8,-1 c0.8,-1.1 2,-1.6 3.3,-0.8 l3,2 c1.5,1 2,2.5 0.5,4 l-1.5,1.5 c-2,2 -7,0 -11,-4 s-6,-9 -4,-11 z" fill="var(--paper)"/>
      <path d="M55,245 a8,8 0 0 1 7,7 M55,240 a13,13 0 0 1 12,12" fill="none" stroke="var(--paper)" stroke-width="2" stroke-linecap="round"/>
      <text class="phone-number" x="83" y="274" font-size="58" textLength="292" lengthAdjust="spacingAndGlyphs">555.201.0148</text>

      <!-- company name -->
      <rect class="company-mark" x="405" y="251" width="44" height="44" fill="var(--brand-blue)"/>
      <text class="company-name" x="463" y="246" font-size="38" textLength="196" lengthAdjust="spacingAndGlyphs">HARBORVIEW</text>
      <text class="company-name" x="463" y="294" font-size="38" textLength="196" lengthAdjust="spacingAndGlyphs">SCREENING</text>

      <!-- diagonal accent stripes -->
      <polygon class="stripe-green" points="792,0 801,0 658,323 649,323" fill="var(--brand-green)"/>
      <polygon class="stripe-blue" points="804,0 816,0 681,323 669,323" fill="var(--brand-blue)"/>

      <!-- porch photo area -->
      <g clip-path="url(#photo-area)">
        <rect x="660" y="0" width="414" height="323" fill="url(#porch-photo-tones)" role="img" aria-label="Photo of a covered, screened coastal porch with wicker lounge chairs, a coffee table and a fenced lawn beyond"/>
        <rect class="photo-frame" x="699" y="21" width="353" height="278" fill="none" stroke="var(--paper)" stroke-width="1.2"/>
      </g>
    </svg>
  </div>
</body>
</html>
```